Web design for sitter site

We will be launching a sitter site in the coming months that focuses on sitters for children. The name of this site will be Kindlebough.com
We will need:
1. main page design
2. site logo designed
3. subpages as well for the look of people's profiles, and job listings, etc (see links below)
We only need the design, photos, font files, etc. We do not need this site coded (no html), a ps job is fine.
Some competing sites in the space include - tendlane.com and brio.com
http://www.pebble-keeper.example/images/profile1.jpg
http://marrowbooks.example/wp-content/uploads/2013/09/brio-review.png
http://www.quillmont.example/hr/photos/tend_lane2.jpg
Thanks for your interest!
Mothers of children, mainly women
Online

```html
<!DOCTYPE html>
<html lang="en">
<head>
<meta charset="utf-8">
<title>Kindlebough.com</title>
<link href="https://fonts.googleapis.com/css2?family=Source+Sans+3:wght@300;400;600&family=Shadows+Into+Light&display=swap" rel="stylesheet">
<style>
:root{
  --ink:#3a3a3a;
  --muted:#8a8a8a;
  --dark:#2a2a2a;
  --green:#6cb24a;
  --green-dark:#559a37;
  --teal:#2aa3c4;
  --light:#f5f5f5;
  --line:#d9d9d9;
  --white:#ffffff;
}
*{margin:0;padding:0;box-sizing:border-box}
html,body{width:686px;height:1200px;overflow:hidden;background:var(--white)}
body{font-family:"Source Sans 3",Arial,sans-serif;color:var(--ink)}
.page{position:relative;width:858px;height:1500px;transform:scale(.8);transform-origin:0 0}
.abs{position:absolute}

/* header */
.topbar{left:0;top:0;width:858px;height:62px;background:var(--dark)}
.brand-mark{left:95px;top:0;width:56px;height:44px;background:var(--white)}
.brand-name{left:162px;top:5px;font-size:24px;font-weight:400;color:var(--white)}
.search{left:603px;top:20px;width:161px;height:24px;background:var(--white);border:1px solid #ccc;display:flex}
.search span{flex:1;font-size:9px;font-style:italic;color:#aaa;padding:6px 10px}
.search i{width:24px;background:#d8d8d8;display:flex;align-items:center;justify-content:center}

.navbar{left:0;top:62px;width:858px;height:35px;background:linear-gradient(#fafafa,#ececec);border-bottom:1px solid #ddd}
.nav{left:97px;top:75px;display:flex;gap:12px;font-size:9px;color:#555;text-transform:uppercase}
.nav b{font-weight:400;color:#999}
.trust{left:532px;top:74px;font-size:9.5px;color:#555}
.signup{left:636px;top:68px;width:128px;height:23px;border:1px solid #ccc;font-size:9.5px;color:#999;padding:5px 8px}
.signup em{font-style:normal;color:#555}

/* hero */
.hero{left:0;top:97px;width:858px;height:514px;background:linear-gradient(100deg,#e8ecef 0%,#f3d3d8 30%,#f2e5de 50%,#e8c3ad 65%,#2d6fb4 85%,#a7d89a 100%)}
.hero-arrow{width:36px;height:36px;border-radius:50%;background:rgba(40,40,40,.75);top:277px}
.choose{left:93px;top:477px;width:672px;height:178px;background:rgba(255,255,255,.93);box-shadow:0 14px 14px -10px rgba(0,0,0,.25)}
.choose h2{position:absolute;left:0;width:100%;top:14px;text-align:center;font-weight:400;font-size:16px;text-transform:uppercase;color:#333}
.option{position:absolute;top:61px;width:271px;height:106px;border:1px solid var(--line);text-align:center}
.option .label{position:absolute;top:-14px;left:50%;transform:translateX(-50%);background:var(--white);padding:0 14px;font-family:"Shadows Into Light",cursive;font-size:17px;line-height:24px;color:#333;white-space:nowrap}
.option .label span{color:var(--teal)}
.option p{margin-top:28px;font-size:10px;color:#555}
.btn{display:inline-block;background:var(--green);color:var(--white);font-size:11.5px;border:1px solid var(--green-dark);text-align:center}
.option .btn{position:absolute;left:62px;top:61px;width:142px;height:29px;line-height:27px}

/* offers */
.section-title{left:0;width:858px;text-align:center;font-size:18px;font-weight:400;color:#333}
.card{top:741px;width:214px;height:202px;background:var(--light)}
.card .photo{height:109px}
.card h3{font-size:14.5px;font-weight:400;margin:12px 11px 7px}
.card p{font-size:9px;line-height:14px;color:var(--muted);margin:0 11px}
.card a{color:var(--green);font-style:italic;text-decoration:none}

/* welcome */
.welcome{left:0;top:987px;width:858px;height:231px;background:var(--light)}
.welcome p{position:absolute;left:108px;width:642px;text-align:center;font-size:9.5px;line-height:16px;color:var(--muted)}
.welcome .btn{position:absolute;left:385px;top:186px;width:88px;height:24px;line-height:22px;font-size:9.5px}

/* testimonial */
.avatar{left:151px;top:1298px;width:80px;height:80px;border-radius:50%;border:3px solid var(--white);box-shadow:0 0 0 1px #ddd;background:radial-gradient(circle,#e9c7b2,#b58a6c)}
.quote{left:253px;top:1316px;width:452px;font-size:9px;line-height:16px;color:var(--muted)}
.quote .mark{font-size:22px;color:#aaa;font-style:italic;vertical-align:-6px;margin-right:4px}
.by{left:253px;top:1376px;font-size:9px;color:var(--green)}

/* footer */
.footer{left:0;top:1428px;width:858px;height:72px;background:var(--dark)}
.foot-links{left:96px;top:1447px;font-size:9px;color:#aaa}
.copy{left:96px;top:1469px;font-size:9px;color:#aaa}
.social{top:1453px;width:20px;height:20px;border-radius:50%;background:#8a8a8a}
</style>
</head>
<body>
<div class="page">
  <header>
    <div class="abs topbar"></div>
    <div class="abs brand-mark"></div>
    <div class="abs brand-name">Kindlebough.com</div>
    <div class="abs search"><span>Search here...</span><i><svg width="12" height="12" viewBox="0 0 12 12"><circle cx="5" cy="5" r="3.5" fill="none" stroke="#555" stroke-width="1.6"/><line x1="7.5" y1="7.5" x2="11" y2="11" stroke="#555" stroke-width="1.8"/></svg></i></div>
    <div class="abs navbar"></div>
    <nav class="abs nav">Home <b>/</b> About Us <b>/</b> Services <b>/</b> Gallery <b>/</b> Blog <b>/</b> Contact Us</nav>
    <div class="abs trust">Trust &amp; Safety Center</div>
    <div class="abs signup">Sign Up : <em>Parents</em> &nbsp;| <em>Sitters</em></div>
  </header>

  <section>
    <div class="abs hero" role="img" aria-label="Photo of a smiling woman playing finger puppets with a toddler at a craft table"></div>
    <div class="abs hero-arrow" style="left:63px"><svg width="36" height="36"><polyline points="21,11 14,18 21,25" fill="none" stroke="#fff" stroke-width="1.5"/></svg></div>
    <div class="abs hero-arrow" style="left:760px"><svg width="36" height="36"><polyline points="15,11 22,18 15,25" fill="none" stroke="#fff" stroke-width="1.5"/></svg></div>
    <div class="abs choose">
      <h2>Let’s get started. Choose an option.</h2>
      <div class="option" style="left:43px">
        <div class="label">I need a <span>caregiver</span></div>
        <p>Start your free search for care in your area.</p>
        <a class="btn">Find Care &gt;&gt;</a>
      </div>
      <div class="option" style="left:358px">
        <div class="label">I want a <span>care job</span></div>
        <p>Create a free profile and search for jobs.</p>
        <a class="btn">Find Jobs &gt;&gt;</a>
      </div>
    </div>
  </section>

  <section>
    <h2 class="abs section-title" style="top:700px">What we offer</h2>
    <div class="abs card" style="left:93px">
      <div class="photo" role="img" aria-label="Photo of a woman with three young children at a colourful table" style="background:linear-gradient(120deg,#f4e6dc,#e8a4a8,#6c8fb8)"></div>
      <h3>For Children Care</h3>
      <p>Donec laoreet metus id laot malesuada. Lorem ipsum dolor sit am consectetur adipiscing elit. In mollis erat mattis. <a>Read More &gt;&gt;</a></p>
    </div>
    <div class="abs card" style="left:322px">
      <div class="photo" role="img" aria-label="Photo of a carer reading a book with an elderly woman" style="background:linear-gradient(120deg,#e9dcd2,#e8a8b0,#c98a7a)"></div>
      <h3>For Elders Care</h3>
      <p>Donec laoreet metus id laot malesuada. Lorem ipsum dolor sit am consectetur adipiscing elit. In mollis erat mattis. <a>Read More &gt;&gt;</a></p>
    </div>
    <div class="abs card" style="left:551px">
      <div class="photo" role="img" aria-label="Photo of a groomer holding a small long-haired dog" style="background:linear-gradient(120deg,#e4e6e0,#d8b98a,#6b3f66)"></div>
      <h3>For Pet Care</h3>
      <p>Donec laoreet metus id laot malesuada. Lorem ipsum dolor sit am consectetur adipiscing elit. In mollis erat mattis. <a>Read More &gt;&gt;</a></p>
    </div>
  </section>

  <section class="abs welcome">
    <h2 class="abs section-title" style="top:19px">Welcome to Kindlebough</h2>
    <p style="top:58px">Vivamus at magna non nunc tristique rhoncus. Aliquam nibh ante, egestas id dictum acommodo luctuslibero. Praesent faucibus malesuada faucibus. Donec laoreet metus id laot malesuada. Lorem ipsum dolor sit am consectetur adipiscing elit. In mollis erat mattis.</p>
    <p style="top:107px">Vivamus at magna non nunc tristique rhoncus. Aliquam nibh ante, egestas id dictum acommodo luctuslibero. Praesent faucibus malesuada faucibus. Donec laoreet metus id laot malesuada. Lorem ipsum dolor sit am consectetur adipiscing elit. In mollis erat mattis. Vivamus at magna non nunc tristique rhoncus. Aliquam nibh ante, egestas id dictum acommodo luctuslibero. Praesent faucibus malesuada faucibus. Donec laoreet metus id laot malesuada. Lorem ipsum dolor sit am consectetur adipiscing elit. In mollis erat mattis.</p>
    <a class="btn">Read More &gt;&gt;</a>
  </section>

  <section>
    <h2 class="abs section-title" style="top:1256px">Client Testimonial</h2>
    <svg class="abs" style="left:106px;top:1329px" width="14" height="14"><polyline points="11,2 4,7 11,12" fill="none" stroke="#6cb24a" stroke-width="3"/></svg>
    <svg class="abs" style="left:738px;top:1329px" width="14" height="14"><polyline points="3,2 10,7 3,12" fill="none" stroke="#6cb24a" stroke-width="3"/></svg>
    <div class="abs avatar" role="img" aria-label="Portrait photo of the client"></div>
    <p class="abs quote"><span class="mark">“</span>Vivamus at magna non nunc tristique rhoncus. Aliquam nibh ante, egestas id dictum acommodo luctus-libero. Praesent faucibus malesuada faucibus. Donec laoreet metus id laot malesuada. Lorem ipsum dolor sit amesoi consectetur adipiscing elit. In mollis erat mattis.</p>
    <div class="abs by">by Mara Ellison</div>
  </section>

  <footer>
    <div class="abs footer"></div>
    <div class="abs foot-links">About Us &nbsp;| &nbsp;Privacy Policy &nbsp;| &nbsp;Site map</div>
    <div class="abs copy">Copyright © 2014 Kindlebough.com. All Rights Reserved.</div>
    <div class="abs social" style="left:669px"></div>
    <div class="abs social" style="left:694px"></div>
    <div class="abs social" style="left:718px"></div>
    <div class="abs social" style="left:742px"></div>
  </footer>
</div>
</body>
</html>
```